Biz Card Design TVCP

New business card for a new company.
Logo was completed by a designer on ArtHarbor and looking to continue requesting additional services.
Company Name: Tidal Vector Power Consulting
Although this company is starting in Canada, we will be moving towards a global presence within the next 6 months.
Key elements to this business are as follows.
Energy Procurement
Energy Reduction Services
Demand Side Consulting
Energy Efficiency Consulting
Saving Clients Money
Helping Them Go "Green"
Managing Their Energy Requirements
Basically the goal for our company is to find the best procurement solution for our clients and reduce their energy consumption. This reduces their expenses and the amount of greenhouse gas they produce on a daily basis.
I have been in the energy footprint for the last 20 years and know that most companies are looking to "do whatever is necessary to get them to sign on the dotted line". I would prefer to walk away from a client that I can't help than to put them into a situation that they will regret for years to come. This is where the "TIDAL" part of the company name comes from.
The following is a catch phrase that encompasses what we do.
"Reducing your carbon footprint & energy bill at the same time!"
The back of the card needs to have this statement along with some sort of illustration. The back is a playground for creative ideas.
The front of the card needs the following.
Logo.
First & Last Name (Gus Marwick)
Title (Energy Warrior)
Phone Number (555) 314-2718
Fax Number (555) 271-8314
Email Address gus@tidalvectorpowerconsulting.example
Address 47 fenwick rd Toronto Ontario K4T 2P9
I want it to be a card that is remembered when any of my staff give it to a customer. It HAS to stand out.
Target Market(s)
Business Owners, Decision Makers, 30 to 65+
Industry/Entity Type
Business
Look and feel

```html
<!DOCTYPE html>
<html lang="en">
<head>
<meta charset="utf-8">
<title>Tidal Vector Power Consulting – Business Card</title>
<link rel="stylesheet" href="https://fonts.googleapis.com/css2?family=Open+Sans:ital,wght@0,400;0,600;0,700;1,700&display=swap">
<style>
  :root {
    --stage: #eceeea;
    --card-dark: #0b0d0b;
    --card-light: #ffffff;
    --green: #2e9e3e;
    --green-dark: #0f8a3c;
    --green-light: #c9e79a;
    --blue: #3a66b8;
    --ink: #5b5b5b;
    --white: #ffffff;
  }
  * { box-sizing: border-box; margin: 0; padding: 0; }
  html, body { width: 1200px; height: 900px; overflow: hidden; }
  body {
    background: var(--stage);
    font-family: "Open Sans", Arial, sans-serif;
    display: flex;
    align-items: center;
    justify-content: center;
    gap: 32px;
  }
  .card {
    position: relative;
    width: 560px;
    height: 320px;
    overflow: hidden;
    box-shadow: 0 8px 22px rgba(0,0,0,.18);
  }
  .tagline-band {
    position: absolute;
    left: 0; right: 0; bottom: 0;
    height: 46px;
    background: linear-gradient(90deg, var(--green-light), var(--green) 60%, var(--green-dark));
    display: flex;
    align-items: center;
    justify-content: center;
    color: var(--white);
    font-weight: 700;
    font-size: 15px;
    white-space: nowrap;
  }
  .brand {
    display: flex;
    align-items: center;
    gap: 10px;
    color: var(--green);
    font-weight: 700;
    font-size: 24px;
    letter-spacing: -.3px;
    white-space: nowrap;
  }
  .brand-dot {
    width: 18px; height: 18px;
    border-radius: 50%;
    background: var(--green);
    flex: none;
  }

  /* back */
  .card-back { background: var(--card-dark); }
  .back-texture {
    position: absolute; inset: 0 0 46px 0;
    background: linear-gradient(160deg, #161a16, #070807);
  }
  .back-content {
    position: absolute;
    left: 0; right: 0; top: 58px;
    display: flex; flex-direction: column; align-items: center;
  }
  .services {
    margin-top: 26px;
    list-style: none;
    color: var(--white);
    font-size: 13px;
    line-height: 1.6;
    text-align: center;
  }
  .services .sep { color: var(--blue); padding: 0 4px; }

  /* front */
  .card-front { background: var(--card-light); }
  .front-accent {
    position: absolute;
    left: -70px; top: 90px;
    width: 200px; height: 200px;
    border-radius: 50%;
    background: radial-gradient(circle at 60% 40%, #c9e79a, #4aa84e 70%, transparent 71%);
    opacity: .85;
  }
  .front-brand { position: absolute; left: 150px; top: 34px; font-size: 21px; }
  .contact {
    position: absolute; right: 24px; top: 92px;
    text-align: right; font-size: 12.5px; line-height: 1.6; color: var(--ink);
    white-space: nowrap;
  }
  .contact .label { color: var(--green); }
  .person { position: absolute; left: 150px; top: 178px; white-space: nowrap; }
  .person-name { font-size: 21px; font-weight: 600; color: var(--green); }
  .person-title { font-size: 14px; color: var(--blue); font-weight: 600; }
  .person-title::before { content: "|"; color: var(--ink); padding: 0 6px; }
  .address { margin-top: 2px; font-size: 14px; color: var(--ink); line-height: 1.4; }
</style>
</head>
<body>

  <article class="card card-back">
    <div class="back-texture" role="img" aria-label="Faint repeating leaf pattern on black"></div>
    <div class="back-content">
      <div class="brand"><span class="brand-dot"></span>Tidal Vector Power Consulting</div>
      <ul class="services">
        <li>Energy Procurement<span class="sep">•</span>Energy Reduction Services<span class="sep">•</span>Demand Side Consulting</li>
        <li>Energy Efficiency Consulting<span class="sep">•</span>Saving Clients Money</li>
        <li>Helping Them Go "Green"<span class="sep">•</span>Managing Their Energy Requirements</li>
      </ul>
    </div>
    <p class="tagline-band">"Reducing your carbon footprint &amp; energy bill at the same time!"</p>
  </article>

  <article class="card card-front">
    <div class="front-accent" role="img" aria-label="Soft green brand accent"></div>
    <div class="brand front-brand"><span class="brand-dot"></span>Tidal Vector Power Consulting</div>
    <div class="contact">
      <p><span class="label">Phone :</span> (555) 314-2718</p>
      <p><span class="label">Fax :</span> (555) 271-8314</p>
      <p>gus@tidalvectorpowerconsulting.example</p>
    </div>
    <div class="person">
      <p><span class="person-name">Gus Marwick</span><span class="person-title">Energy Warrior</span></p>
      <p class="address">47 fenwick rd Toronto<br>Canada K4T 2P9</p>
    </div>
    <p class="tagline-band">"Reducing your carbon footprint &amp; energy bill at the same time!"</p>
  </article>

</body>
</html>
```